Investigation Before Elimination

Create a very professional and eye-catching Infographic for Birch Supply that is intended to convey to retailers that they should investigate why products are NOT selling in the Birch Supply store before they apply a discount to get rid of it. The infographic should capture all of the questions they should think about before making cutting the price. See the attachment for details on wording.

Target Market(s)

Birch Supply Business Owners

Industry/Entity Type

Retail

Font styles to use
Sans Serif

Requirements
Must have
• Any product in the infographic must be home improvement related product. See our website for ideas:
https://www.birchsupply.example/?utm_source=google&utm_medium=cpc&gclid=QxwPLMnt4R2FTkBkLpwD8WXYM5n_qa3HTkvb9aJ742_9Rm-dpLzk9Tnm80vt5zXrJg0b6-Ydxk7-vNZPm-kqEtnPAwD_BwE&gclsrc=aw.ds

* Must be in Birch Supply related colors
* Must be fun, exciting, eye-catching, unique, and clever
* 1-Page preferable but no more than two standard 8-1/2"x11"
* See the attachment for details on wording.
Should not have
• N/A

```html
<!DOCTYPE html>
<html lang="en">
<head>
<meta charset="utf-8">
<title>Investigation Before Elimination – Birch Supply</title>
<link href="https://fonts.googleapis.com/css2?family=Roboto+Slab:wght@700&family=Roboto:wght@400;500;700&display=swap" rel="stylesheet">
<style>
:root{
  --ink:#3b3b3b;
  --ink-dark:#444343;
  --red:#d9202f;
  --green:#8cc63f;
  --blue:#6fb3dc;
  --purple:#8e5c9e;
  --pink:#e5307d;
  --crimson:#b5202e;
  --scarlet:#e3263a;
  --orange:#f08a24;
  --teal:#2bb5a0;
  --footer-light:#e4e4e4;
  --footer-dark:#6d6a6a;
  --white:#ffffff;
}
*{margin:0;padding:0;box-sizing:border-box}
html,body{width:927px;height:1200px;overflow:hidden;background:var(--white)}
body{font-family:"Roboto",Arial,sans-serif;color:var(--ink)}
.sheet{position:relative;width:927px;height:1200px;overflow:hidden}
.graphic{position:absolute;left:0;top:0}
.title-top,.title-bottom{position:absolute;font-family:"Roboto Slab",Georgia,serif;font-weight:700;line-height:1;letter-spacing:-.5px}
.title-top{left:98px;top:64px;font-size:56px;color:var(--ink-dark)}
.title-bottom{left:192px;top:115px;font-size:56px;color:var(--red)}
.title-before{position:absolute;left:55px;top:125px;width:128px;height:37px;background:var(--ink-dark);color:var(--white);font-family:"Roboto Slab",Georgia,serif;font-weight:400;font-size:27px;line-height:37px;text-align:center;letter-spacing:.5px}
.brand{position:absolute;left:700px;top:92px;display:flex;align-items:center;gap:10px;font-family:"Roboto",Arial,sans-serif;font-weight:700;font-size:34px;color:var(--red)}
.brand-mark{width:22px;height:22px;background:var(--red)}
.divider{position:absolute;left:55px;top:182px;width:818px;border-top:2px dotted #9a9a9a}
.lead{position:absolute;left:55px;top:195px;width:820px;font-size:20px;font-weight:700;line-height:26px;color:var(--ink)}
.intro{position:absolute;left:55px;top:304px;width:820px;font-size:15px;line-height:20px;color:var(--ink)}
.verdict{position:absolute;left:70px;top:542px;width:338px;text-align:center;color:var(--white);font-size:21px;line-height:27px}
.verdict .yes{background:var(--red);font-weight:700;padding:0 4px}
.verdict .go{color:var(--red);font-weight:700;font-size:15px}
.step{position:absolute;font-size:12.5px;line-height:15px;color:var(--ink)}
.step h3{font-size:14px;line-height:16px;font-weight:700;margin-bottom:1px}
.step-1{left:355px;top:360px;width:300px}.step-1 h3{color:var(--green)}
.step-2{left:487px;top:421px;width:260px}.step-2 h3{color:var(--blue)}
.step-3{left:568px;top:501px;width:250px}.step-3 h3{color:var(--purple)}
.step-4{left:600px;top:613px;width:250px}.step-4 h3{color:var(--pink)}
.step-5{left:600px;top:716px;width:240px}.step-5 h3{color:var(--crimson)}
.step-6{left:565px;top:822px;width:300px}.step-6 h3{color:var(--scarlet)}
.step-7{left:487px;top:926px;width:300px}.step-7 h3{color:var(--orange)}
.step-8{left:362px;top:989px;width:320px}.step-8 h3{color:var(--teal)}
.resources{position:absolute;left:0;top:1062px;width:927px;height:84px;background:var(--footer-light);text-align:center;padding-top:12px;font-size:15px;line-height:21px;color:var(--ink)}
.resources .links{color:var(--red)}
.resources .sep{color:#8a8a8a;margin:0 6px}
.contact-bar{position:absolute;left:0;top:1146px;width:927px;height:54px;background:var(--footer-dark);color:var(--white);font-size:15px;display:flex;align-items:center;padding-left:65px;gap:8px}
.contact-bar .stripe-dark{position:absolute;left:0;top:0;width:22px;height:54px;background:#4a4848}
.contact-bar .stripe-red{position:absolute;left:22px;top:0;width:18px;height:54px;background:var(--red)}
.contact-bar svg{flex:none}
.contact-bar .gap{width:14px}
</style>
</head>
<body>
<div class="sheet">

<svg class="graphic" width="927" height="1200" viewBox="0 0 927 1200" aria-hidden="false">
  <defs>
    <clipPath id="lower-half">
      <rect x="40" y="695" width="400" height="220"/>
    </clipPath>
    <linearGradient id="scene-tone" x1="0" y1="0" x2="0" y2="1">
      <stop offset="0" stop-color="#7a5a3e"/>
      <stop offset=".55" stop-color="#4a4a4c"/>
      <stop offset="1" stop-color="#8c8a84"/>
    </linearGradient>
  </defs>

  <!-- side bands -->
  <rect x="0" y="415" width="238" height="90" fill="var(--green)"/>
  <rect x="0" y="925" width="238" height="90" fill="var(--teal)"/>

  <!-- ring segments -->
  <path d="M238 415 A300 300 0 0 1 352.8 437.8 L318.4 521 A210 210 0 0 0 238 505Z" fill="var(--green)"/>
  <path d="M352.8 437.8 A300 300 0 0 1 450.1 502.9 L386.5 566.5 A210 210 0 0 0 318.4 521Z" fill="var(--blue)"/>
  <path d="M450.1 502.9 A300 300 0 0 1 515.2 600.2 L432 634.6 A210 210 0 0 0 386.5 566.5Z" fill="var(--purple)"/>
  <path d="M515.2 600.2 A300 300 0 0 1 538 715 L448 715 A210 210 0 0 0 432 634.6Z" fill="var(--pink)"/>
  <path d="M538 715 A300 300 0 0 1 515.2 829.8 L432 795.4 A210 210 0 0 0 448 715Z" fill="var(--crimson)"/>
  <path d="M515.2 829.8 A300 300 0 0 1 450.1 927.1 L386.5 863.5 A210 210 0 0 0 432 795.4Z" fill="var(--scarlet)"/>
  <path d="M450.1 927.1 A300 300 0 0 1 352.8 992.2 L318.4 909 A210 210 0 0 0 386.5 863.5Z" fill="var(--orange)"/>
  <path d="M352.8 992.2 A300 300 0 0 1 238 1015 L238 925 A210 210 0 0 0 318.4 909Z" fill="var(--teal)"/>
  <!-- soft inner stripe -->
  <path d="M238 505 A210 210 0 0 1 238 925 L238 909 A194 194 0 0 0 238 521Z" fill="#ffffff" opacity=".4"/>

  <!-- centre disc -->
  <circle cx="238" cy="715" r="193" fill="var(--ink-dark)"/>
  <g role="img" aria-label="Photo of outdoor grills and a bag of charcoal on a wooden deck">
    <circle cx="238" cy="715" r="193" fill="url(#scene-tone)" clip-path="url(#lower-half)"/>
  </g>

  <!-- segment icons -->
  <g fill="none" stroke="#fff" stroke-width="2" stroke-linejoin="round" stroke-linecap="round">
    <path d="M274 458 l14-7 14 7 v16 l-14 7 -14-7z M274 458 l14 7 14-7 M288 465 v16"/>
    <path d="M364 490 h32 M364 503 h32 M364 516 h32 M366 490 v28 M394 490 v28 M370 484 h8 v6 M382 497 h8 v6"/>
    <path d="M440 562 l14 0 10 10 -14 14 -10-10z"/><circle cx="445" cy="567" r="2" stroke="#fff"/>
    <path d="M474 660 l14-6 14 6 v14 l-14 6 -14-6z M474 660 l14 6 14-6 M488 666 v14 M488 646 v-6 M480 648 l-3-4 M496 648 l3-4"/>
    <path d="M474 754 h-2 v-6 h6 M502 754 h2 v-6 h-6 M474 776 h-2 v6 h6 M502 776 h2 v6 h-6"/><circle cx="492" cy="764" r="6"/><path d="M496 769 l6 6"/>
    <path d="M434 846 h6 l5 16 h14 l4-11 h-21"/><circle cx="447" cy="867" r="2"/><circle cx="458" cy="867" r="2"/>
    <path d="M364 922 h32 l-4 14 h-24z M372 922 l6-10 M388 922 l-6-10 M374 927 v5 M380 927 v5 M386 927 v5"/>
    <path d="M277 952 h18 l4 4 v20 h-22z"/><path d="M281 960 h12 M281 966 h12 M281 971 h8"/>
  </g>

  <!-- number badges & connectors -->
  <g font-family="Roboto,Arial,sans-serif" font-weight="700" font-size="17" fill="#fff" text-anchor="middle">
    <line x1="327" y1="385" x2="348" y2="385" stroke="var(--green)" stroke-width="1.5"/><circle cx="348" cy="385" r="2.5" fill="var(--green)"/>
    <circle cx="305" cy="385" r="22" fill="var(--green)"/><text x="305" y="391">01</text>
    <line x1="447" y1="440" x2="480" y2="440" stroke="var(--blue)" stroke-width="1.5"/><circle cx="480" cy="440" r="2.5" fill="var(--blue)"/>
    <circle cx="425" cy="440" r="22" fill="var(--blue)"/><text x="425" y="446">02</text>
    <line x1="529" y1="533" x2="561" y2="533" stroke="var(--purple)" stroke-width="1.5"/><circle cx="561" cy="533" r="2.5" fill="var(--purple)"/>
    <circle cx="507" cy="533" r="22" fill="var(--purple)"/><text x="507" y="539">03</text>
    <line x1="569" y1="641" x2="593" y2="641" stroke="var(--pink)" stroke-width="1.5"/><circle cx="593" cy="641" r="2.5" fill="var(--pink)"/>
    <circle cx="547" cy="641" r="22" fill="var(--pink)"/><text x="547" y="647">04</text>
    <line x1="571" y1="747" x2="593" y2="747" stroke="var(--crimson)" stroke-width="1.5"/><circle cx="593" cy="747" r="2.5" fill="var(--crimson)"/>
    <circle cx="549" cy="747" r="22" fill="var(--crimson)"/><text x="549" y="753">05</text>
    <line x1="486" y1="853" x2="458" y2="853" stroke="var(--scarlet)" stroke-width="1.5"/>
    <circle cx="508" cy="853" r="22" fill="var(--scarlet)"/><text x="508" y="859">06</text>
    <line x1="427" y1="923" x2="427" y2="905" stroke="var(--orange)" stroke-width="1.5"/><line x1="449" y1="945" x2="480" y2="945" stroke="var(--orange)" stroke-width="1.5"/><circle cx="480" cy="945" r="2.5" fill="var(--orange)"/>
    <circle cx="427" cy="945" r="22" fill="var(--orange)"/><text x="427" y="951">07</text>
    <line x1="300" y1="980" x2="292" y2="968" stroke="var(--teal)" stroke-width="1.5"/><line x1="335" y1="1000" x2="355" y2="1000" stroke="var(--teal)" stroke-width="1.5"/><circle cx="355" cy="1000" r="2.5" fill="var(--teal)"/>
    <circle cx="313" cy="1000" r="22" fill="var(--teal)"/><text x="313" y="1006">08</text>
  </g>
</svg>

<h1>
  <span class="title-top">INVESTIGATION</span>
  <span class="title-before">BEFORE</span>
  <span class="title-bottom">ELIMINATION</span>
</h1>

<div class="brand"><span class="brand-mark"></span>Birch Supply</div>

<div class="divider"></div>

<p class="lead">Dead stock in your store rapidly eats away at profits, drives up the cost of doing business, and occupies valuable shelf space that would be better served by fresh and more productive products. To address this issue, a typical knee-jerk response is marking down the product and attempting to sell it at a discount.</p>

<p class="intro">Though this is a better approach than simply hoping it sells ‘one day’, applying a markdown should be used only as a last resort after sales floor investigation takes place for common execution issues that are known to hamper sales;</p>

<p class="verdict">It is only after<br>saying <span class="yes">“YES”</span> to these<br>questions should an item<br>be considered for a markdown<br>strategy <span class="go">&gt;&gt;</span></p>

<div class="step step-1"><h3>Is the product physically there?</h3>One of the most typical issues is that the item is no longer existent (i.e. ghost inventory).</div>
<div class="step step-2"><h3>Is the item merchandised properly - Is it in plain view of the customer?</h3>Find out if it is stuck in the backroom, top stock, or buried behind other products.</div>
<div class="step step-3"><h3>Is the item priced competitively?</h3>In today’s price sensitive market, making sure the cost of the SKU is in line with the customer expectation is key.</div>
<div class="step step-4"><h3>Is the physical product and packaging in a desirable condition?</h3>Bottom-line: Nobody wants ripped or torn, or physically abused merchandise.</div>
<div class="step step-5"><h3>Is the sale of the SKU independent of the sale of another item?</h3>With SKUs that depend on each other to sell, analyze the sell through and performance of the other item.</div>
<div class="step step-6"><h3>Do you have enough quantity of the item for the customer to want to make the purchase?</h3>Seldom do consumers come in to buy one or two casters (i.e. project SKU). Having sufficient quantity to sell the job quantity is key</div>
<div class="step step-7"><h3>Is the item still relevant to the shopper?</h3>Get rid of outdated product and technology.. those old rotary dial phone cords!</div>
<div class="step step-8"><h3>Is the item unique enough to where an alike SKU &nbsp;isn’t cannibalizing its sales?</h3>Each SKU needs to be different and stand on its own. Eliminate redundancies in the product mix.</div>

<div class="resources">
  For further detail on in-stock position, see the following resources:<br>
  <span class="links">Obsolete Inventory - Closeout Management (COM) Setup</span><span class="sep">|</span><span class="links">In-Stock Procedures</span><span class="sep">|</span><span class="links">Markdown Strategy</span><br>
  Visit: https://hub.birchsupply.example/ops/inventory-management
</div>

<div class="contact-bar">
  <span class="stripe-dark"></span><span class="stripe-red"></span>
  <span>For more information, contact Store Systems and Operations:</span>
  <svg width="22" height="22" viewBox="0 0 22 22" aria-label="Phone"><circle cx="11" cy="11" r="9.5" fill="none" stroke="#fff" stroke-width="1.5"/><path d="M7.5 6.5 l2 -.5 1 2.5 -1.2 1 a6 6 0 0 0 3 3 l1-1.2 2.5 1 -.5 2 c-4 .5 -8.3-3.8-7.8-7.8z" fill="#fff"/></svg>
  <span>555.014.2270</span>
  <span class="gap"></span>
  <svg width="24" height="18" viewBox="0 0 24 18" aria-label="Email"><rect x="1" y="1" width="22" height="16" fill="none" stroke="#fff" stroke-width="1.5"/><path d="M1 1 l11 9 11-9" fill="none" stroke="#fff" stroke-width="1.5"/></svg>
  <span>storeoperations@birchsupply.example</span>
</div>

</div>
</body>
</html>
```